New Company Business Card design

Looking for a corporate looking business card utilising my new logo design - the logo i would like embossed as one option and flat as another - simplistic but stylish - less is more - we are an import export business launching into the market - i would like a couple of options as main background - Grey or Black

```html
<!DOCTYPE html>
<html lang="en">
<head>
<meta charset="utf-8">
<title>Meridian Trade Partners – Business Card</title>
<link rel="stylesheet" href="https://fonts.googleapis.com/css2?family=Roboto:wght@400;500;700&family=Roboto+Condensed:wght@700&display=swap">
<style>
  :root {
    --backdrop: #d9d6d1;
    --card-black: #19191b;
    --card-blue: #1674bf;
    --card-navy: #0a3152;
    --accent-grey: #6a6b6e;
    --text-white: #ffffff;
    --brand-blue: #1a78c2;
  }
  html, body {
    margin: 0;
    padding: 0;
    width: 1200px;
    height: 960px;
    overflow: hidden;
    background: var(--backdrop);
    font-family: "Roboto", Arial, sans-serif;
  }
  .canvas {
    position: relative;
    width: 1200px;
    height: 960px;
  }
  .card {
    position: absolute;
    width: 600px;
    height: 342px;
    overflow: hidden;
    box-shadow: 0 3px 8px rgba(0,0,0,0.35);
  }
  .card-front { left: 314px; top: 113px; background: var(--card-blue); }
  .card-back  { left: 312px; top: 472px; background: var(--card-navy); }
  .card-shapes {
    position: absolute;
    inset: 0;
    width: 600px;
    height: 342px;
  }
  .brand-name {
    position: absolute;
    margin: 0;
    font-family: "Roboto", Arial, sans-serif;
    font-weight: 500;
    white-space: nowrap;
  }
  .card-front .brand-name {
    left: 40px;
    top: 202px;
    width: 262px;
    text-align: center;
    font-size: 16px;
    letter-spacing: 0.5px;
    color: var(--brand-blue);
  }
  .contact {
    position: absolute;
    left: 356px;
    top: 56px;
    color: var(--text-white);
  }
  .contact-name {
    margin: 0;
    font-family: "Roboto Condensed", Arial, sans-serif;
    font-weight: 700;
    font-size: 23px;
    line-height: 26px;
  }
  .contact-title {
    margin: 1px 0 0;
    font-family: "Roboto Condensed", Arial, sans-serif;
    font-weight: 700;
    font-size: 14px;
  }
  .contact-address {
    margin: 46px 0 8px;
    font-size: 14px;
    line-height: 18px;
    font-style: normal;
  }
  .contact-list {
    list-style: none;
    margin: 0;
    padding: 0;
    font-size: 14px;
    line-height: 19.3px;
  }
  .contact-list li {
    display: flex;
    align-items: center;
    gap: 10px;
  }
  .contact-list svg {
    width: 13px;
    height: 13px;
    fill: var(--text-white);
    flex: none;
  }
  .card-back .brand-name {
    left: 26px;
    top: 262px;
    font-size: 18px;
    letter-spacing: 1px;
    color: var(--text-white);
  }
  .back-url {
    position: absolute;
    left: 26px;
    top: 304px;
    margin: 0;
    font-size: 14px;
    color: var(--text-white);
  }
</style>
</head>
<body>
<main class="canvas">

  <section class="card card-front" aria-label="Card front">
    <svg class="card-shapes" viewBox="0 0 600 342" aria-hidden="true">
      <path d="M0 0 H164 C335 60 416 230 200 342 H0 Z" fill="var(--accent-grey)"/>
      <path d="M0 0 H149 C320 60 400 230 186 342 H0 Z" fill="var(--card-black)"/>
    </svg>
    <p class="brand-name">MERIDIAN TRADE PARTNERS</p>

    <div class="contact">
      <h1 class="contact-name">DANIEL REYES</h1>
      <p class="contact-title">CEO/FOUNDER</p>
      <address class="contact-address">412 Harbor View Road<br>Juneau, Alaska 99801</address>
      <ul class="contact-list">
        <li><svg viewBox="0 0 24 24"><path d="M6.6 10.8a15.1 15.1 0 0 0 6.6 6.6l2.2-2.2a1 1 0 0 1 1-.25 11.4 11.4 0 0 0 3.6.57 1 1 0 0 1 1 1V20a1 1 0 0 1-1 1A17 17 0 0 1 3 4a1 1 0 0 1 1-1h3.5a1 1 0 0 1 1 1c0 1.25.2 2.45.57 3.6a1 1 0 0 1-.25 1z"/></svg>907 555 0142</li>
        <li><svg viewBox="0 0 24 24"><path d="M7 1h10a2 2 0 0 1 2 2v18a2 2 0 0 1-2 2H7a2 2 0 0 1-2-2V3a2 2 0 0 1 2-2zm0 3v14h10V4zm5 15.5a1.2 1.2 0 1 0 0 2.4 1.2 1.2 0 0 0 0-2.4z"/></svg>907 555 0187</li>
        <li><svg viewBox="0 0 24 24"><path d="M6 2h12v5H6zM3 8h18a2 2 0 0 1 2 2v7h-4v5H5v-5H1v-7a2 2 0 0 1 2-2zm4 8v4h10v-4z"/></svg>907 555 0163</li>
        <li><svg viewBox="0 0 24 24"><path d="M2 5h20v14H2zm2 2v.5l8 5 8-5V7z"/></svg>hello@meridiantrade.com</li>
        <li><svg viewBox="0 0 24 24"><path d="M12 2a10 10 0 1 0 0 20 10 10 0 0 0 0-20zm-1 17.9A8 8 0 0 1 4.2 10.6L9 15.4v1a2 2 0 0 0 2 2zm6.9-2.5A2 2 0 0 0 16 16h-1v-3a1 1 0 0 0-1-1H8v-2h2a1 1 0 0 0 1-1V7h2a2 2 0 0 0 2-2v-.4a8 8 0 0 1 2.9 12.8z"/></svg>www.meridiantrade.com</li>
      </ul>
    </div>
  </section>

  <section class="card card-back" aria-label="Card back">
    <svg class="card-shapes" viewBox="0 0 600 342" aria-hidden="true">
      <circle cx="500" cy="172" r="200" fill="var(--accent-grey)"/>
    </svg>
    <p class="brand-name">MERIDIAN TRADE PARTNERS</p>
    <p class="back-url">www.meridiantradepartners.com</p>
  </section>

</main>
</body>
</html>
```